KORVEL Group Pty Ltd. Website and Domain

www.korvelgroup.com.au

require email addresses setup.

Info@korvelgroup.com.au
accounts@korvelgroup.com.au
peter.halloway@korvelgroup.com.au
grant.whitley@korvelgroup.com.au

Website should promote commercial and domestic electrical services, audio visual services and data and fibre installations.

similar to my mates site www.brisvane.com.au

Website needs to promote professionalism, electrical/electrician, audio visual and data/fibre cabling installations.

promote environmental friendly imaginary.

Coding

```html
<!DOCTYPE html>
<html lang="en">
<head>
<meta charset="utf-8">
<title>KORVEL Group – Electrical, Audio Visual &amp; Data</title>
<link href="https://fonts.googleapis.com/css2?family=Montserrat:wght@400;500;600;700;800&display=swap" rel="stylesheet">
<style>
  :root{
    --green:#a9cf46;
    --blue:#34a9df;
    --ink:#1d1d1d;
    --muted:#6a6a6a;
    --white:#ffffff;
    --field:#ffffff;
  }
  *{box-sizing:border-box;margin:0;padding:0}
  html,body{width:1200px;height:3907px;overflow:hidden;background:var(--white)}
  body{position:relative;font-family:"Montserrat",Arial,sans-serif;color:var(--ink)}

  /* header */
  .site-header{position:absolute;left:0;top:0;width:1200px;height:94px;background:var(--white);border-top:3px solid var(--green);z-index:5}
  .brand{position:absolute;left:144px;top:22px;display:flex;align-items:center}
  .brand-name{font-size:40px;font-weight:600;color:var(--blue);letter-spacing:2px;line-height:48px}
  .main-nav{position:absolute;top:36px;left:472px;font-size:14px;font-weight:500}
  .main-nav a{position:absolute;white-space:nowrap;color:var(--ink);text-decoration:none}
  .main-nav a.active::after{content:"";position:absolute;left:0;right:0;bottom:-9px;height:3px;background:var(--green)}
  .social{position:absolute;display:flex;gap:6px}
  .social span{width:36px;height:36px;border-radius:50%;background:var(--blue);display:block}

  /* hero */
  .hero{position:absolute;left:0;top:94px;width:1200px;height:780px;overflow:hidden}
  .hero-photo{position:absolute;inset:0;background:linear-gradient(100deg,#7d7771 0%,#b8b0a6 25%,#5a5550 55%,#2b2a2c 80%,#3a3634 100%)}
  .hero-title{position:absolute;left:0;width:1200px;top:188px;text-align:center;font-size:84px;font-weight:800;color:var(--white);text-shadow:0 3px 8px rgba(0,0,0,.45);letter-spacing:1px;line-height:100px}
  .hero-sub{position:absolute;left:0;width:1200px;top:304px;text-align:center;font-size:22px;font-weight:500;color:var(--white);text-shadow:0 2px 5px rgba(0,0,0,.5)}
  .btn{position:absolute;display:flex;align-items:center;justify-content:center;background:var(--green);color:var(--white);font-weight:600;font-size:18px;border-radius:31px;height:61px;letter-spacing:.3px;text-decoration:none}
  .dots{position:absolute;top:598px;left:561px;display:flex;gap:6px}
  .dots i{width:11px;height:11px;border-radius:50%;background:var(--white);display:block}
  .dots i.on{background:var(--green)}
  .wave{position:absolute;left:0;width:1200px}

  /* welcome */
  .section-title{position:absolute;left:0;width:1200px;text-align:center;font-size:42px;font-weight:700;letter-spacing:.5px;line-height:52px}
  .section-title .light{font-weight:400;color:var(--blue)}
  .section-title .g{color:var(--green)}
  .welcome-text{position:absolute;left:160px;width:880px;top:1012px;text-align:center;font-size:16px;line-height:32px;color:var(--muted)}

  /* industrial band */
  .feature-photo{position:absolute;left:0;top:1259px;width:1200px;height:658px;background:linear-gradient(90deg,#c9d3d6 0%,#a9b9be 30%,#c5612e 42%,#8a9aa0 55%,#b7b4ab 75%,#7f7d77 100%)}

  /* services */
  .service{position:absolute;width:285px;text-align:center}
  .service-img{width:285px;height:268px}
  .service h3{font-size:22px;font-weight:500;line-height:29px;margin-top:34px;color:var(--ink)}
  .service p{font-size:13.5px;line-height:21px;color:var(--muted);margin-top:16px;padding:0 8px}

  /* contact */
  .contact{position:absolute;left:0;top:2847px;width:1200px;height:780px;background:linear-gradient(180deg,#35a9df 0%,#3aaee2 100%)}
  .contact-photo{position:absolute;inset:0;background:radial-gradient(ellipse at 25% 40%,rgba(20,90,140,.28),transparent 55%),radial-gradient(ellipse at 85% 70%,rgba(20,90,140,.22),transparent 50%)}
  .contact-title{color:var(--white)}
  .contact-title .light{color:var(--white)}
  .field{position:absolute;background:var(--field);font-size:14px;color:#555;padding:18px 22px}

  /* footer */
  .footer-brand{position:absolute;left:0;width:1200px;top:3640px;text-align:center}
  .footer-brand .brand-name{font-size:52px;line-height:64px}
  .footer-nav{position:absolute;top:3743px;left:0;width:1200px;display:flex;justify-content:center;gap:48px;font-size:20px;font-weight:500}
  .copyright{position:absolute;top:3796px;left:0;width:1200px;text-align:center;font-size:14px;color:#555}
</style>
</head>
<body>

<header class="site-header">
  <div class="brand"><span class="brand-name">KORVEL</span></div>
  <nav class="main-nav">
    <a class="active" style="left:0">HOME</a>
    <a style="left:83px">ABOUT US</a>
    <a style="left:195px">SERVICES</a>
    <a style="left:303px">NEWS</a>
    <a style="left:385px">CONTACT US</a>
  </nav>
  <div class="social" style="left:976px;top:27px"><span></span><span></span></div>
</header>

<section class="hero">
  <div class="hero-photo" role="img" aria-label="Photo of a modern living room with sofa, TV and wall shelves"></div>
  <h1 class="hero-title">KORVEL GROUP</h1>
  <p class="hero-sub">Lorem ipsum dolor sit amet consectetur adipiscing elit</p>
  <a class="btn" style="left:505px;top:385px;width:190px">GET STARTED</a>
  <div class="dots"><i></i><i></i><i class="on"></i><i></i><i></i></div>
  <svg class="wave" style="top:0" width="1200" height="780" viewBox="0 0 1200 780">
    <path d="M0 680 C180 850 420 800 620 700 C820 610 1030 640 1200 700 L1200 780 L0 780Z" fill="#fff"/>
    <path d="M0 690 C180 860 420 812 620 712 C820 620 1030 650 1200 716" fill="none" stroke="var(--blue)" stroke-width="12"/>
    <path d="M0 676 C180 842 420 796 620 696 C820 606 1030 632 1200 696" fill="none" stroke="var(--green)" stroke-width="12"/>
  </svg>
</section>

<h2 class="section-title" style="top:922px">WELCOMR TO <span class="light">KORVEL <span class="g">GR</span>OUP</span></h2>
<p class="welcome-text">Lorem ipsum dolor sit amet, consectetur adipiscing elit, sed do eiusmod tempor incididunt ut labore et dolore magna uis ipsum suspendisse ultrices grcommodo viverra maecenas accumsan lacus vel facilisis. Lorem ipsum dolor sit amet, consectetur adipiscing elit, sed do eiusmod tempor incididunt ut labore et dolore magna uis ipsum suspendisse ultrices grcommodo viverra maecenas accumsan lacus vel facilisis. Lorem ipsum dolor sit amet, consectetur adipiscing elit, sed do eiusmod tempor incididunt ut labore et dolore magna uis ipsum suspendisse ultrices grcommodo viverra maecenas accumsan lacus vel facilisis.</p>

<div class="feature-photo" role="img" aria-label="Photo of an electrician in orange overalls and hard hat testing equipment in an industrial plant"></div>
<svg class="wave" style="top:1259px" width="1200" height="110" viewBox="0 0 1200 110">
  <path d="M0 0 L1200 0 L1200 45 C1080 10 950 0 820 2 C700 5 620 40 560 60 C420 30 200 20 0 60Z" fill="#fff"/>
  <path d="M40 60 C160 25 420 25 560 60 C430 80 160 80 40 60Z" fill="var(--green)"/>
</svg>

<h2 class="section-title" style="top:2013px">OUR <span class="light">SERVICES</span></h2>

<div class="service" style="left:144px;top:2165px">
  <div class="service-img" role="img" aria-label="Photo of an electrician working on a commercial switchboard" style="background:linear-gradient(135deg,#8a8d90,#2c2f33 60%,#d9dadb)"></div>
  <h3>Commercial<br>Electrical Services</h3>
  <p>Lorem ipsum dolor sit ameconsectetur adipiscing elit, sed do eiusmod tempor incididunt ut labore et dolore magna aluspendisse ultrices gravida</p>
</div>
<div class="service" style="left:458px;top:2127px">
  <div class="service-img" role="img" aria-label="Photo of a technician repairing a domestic appliance with a tool kit" style="height:306px;background:linear-gradient(160deg,#bfc2c4,#8d9093 50%,#2d3e8f 85%)"></div>
  <h3>Domestic<br>Electrical Services</h3>
  <p>Lorem ipsum dolor sit ameconsectetur adipiscing elit, sed do eiusmod tempor incididunt ut labore et dolore magna aluspendisse ultrices gravida</p>
</div>
<div class="service" style="left:771px;top:2165px">
  <div class="service-img" role="img" aria-label="Photo of a sound technician at an audio mixing desk" style="background:linear-gradient(160deg,#15184a,#1c2a7a 60%,#3b5ad0)"></div>
  <h3>Audio Visual<br>services</h3>
  <p>Lorem ipsum dolor sit ameconsectetur adipiscing elit, sed do eiusmod tempor incididunt ut labore et dolore magna aluspendisse ultrices gravida</p>
</div>

<a class="btn" style="left:463px;top:2693px;width:274px">VIEW MORE SERVICES</a>

<section class="contact">
  <div class="contact-photo" role="img" aria-label="Blue-tinted photo of two people installing equipment"></div>
  <h2 class="section-title contact-title" style="top:100px">CONTACT <span class="light">FORM</span></h2>
  <div class="field" style="left:234px;top:201px;width:359px;height:52px">First Name</div>
  <div class="field" style="left:605px;top:201px;width:360px;height:52px">Last Name</div>
  <div class="field" style="left:234px;top:264px;width:359px;height:52px">Email address</div>
  <div class="field" style="left:605px;top:264px;width:360px;height:52px">Phone Number</div>
  <div class="field" style="left:234px;top:331px;width:731px;height:112px">Message</div>
  <a class="btn" style="left:463px;top:487px;width:274px">SUBMIT MESSAGE</a>
  <svg class="wave" style="top:600px" width="1200" height="180" viewBox="0 0 1200 180">
    <path d="M0 100 C200 170 420 160 620 100 C820 40 1020 20 1200 100 L1200 180 L0 180Z" fill="#fff"/>
    <path d="M0 112 C200 182 420 172 620 112 C820 52 1020 32 1200 112" fill="none" stroke="var(--blue)" stroke-width="12"/>
    <path d="M0 98 C200 168 420 158 620 98 C820 38 1020 18 1200 98" fill="none" stroke="var(--green)" stroke-width="12"/>
  </svg>
</section>

<footer>
  <div class="footer-brand"><span class="brand-name">KORVEL</span></div>
  <nav class="footer-nav"><span>HOME</span><span>ABOUT US</span><span>SERVICES</span><span>NEWS</span><span>CONTACT US</span></nav>
  <p class="copyright">© 2020 Korvel Group.All Rights reserved &nbsp;|&nbsp; Privacy Policy</p>
  <div class="social" style="left:561px;top:3840px"><span></span><span></span></div>
</footer>

</body>
</html>
```